e-commerce store for sport clothing online store "baseball merchandise "web application...

I want to design a UX/UI for my web application website for the online store I will provide you with the following:
1. screen shots of the initial design for the pages>
2. the logo files.
3. The brand guideline file.

the provided files (screen shots) is guideline I want to see CREATIVITY with the UX/UI DESIGN.
PS. PLEASE FOLLOW THE BRANDGUIDE LINE CAREFULLY SPECIALLY THE TYPOGRAPHY & THE COLOR CODES.

PLEASE VISIT THIS WEBSITE brightlane.varomi-qz.com to see more for the screens.

```html
<!DOCTYPE html>
<html lang="en">
<head>
<meta charset="utf-8">
<title>Diamondline Store – Products and Cart</title>
<link rel="stylesheet" href="https://fonts.googleapis.com/css2?family=IBM+Plex+Sans:wght@400;500;600;700&display=swap">
<style>
  :root {
    --stage: #94969c;
    --surface: #ffffff;
    --content: #f5f4f4;
    --brand-red: #b3102e;
    --ink: #1f2a44;
    --ink-soft: #2b2b2b;
    --line: #ececec;
  }
  * { box-sizing: border-box; margin: 0; padding: 0; }
  html, body { width: 745px; height: 1200px; overflow: hidden; }
  body {
    background: var(--stage);
    font-family: "IBM Plex Sans", Arial, sans-serif;
    color: var(--ink-soft);
    position: relative;
  }
  .screen {
    position: absolute;
    left: 54px;
    width: 643px;
    background: var(--content);
    overflow: hidden;
  }
  .screen--products { top: 55px; height: 516px; }
  .screen--cart { top: 606px; height: 515px; }

  .sidebar {
    position: absolute; left: 0; top: 0; bottom: 0; width: 107px;
    background: var(--surface);
    box-shadow: 1px 0 2px rgba(0,0,0,0.04);
    z-index: 2;
  }
  .brand {
    position: absolute; left: 0; right: 0; top: 34px;
    display: flex; align-items: center; justify-content: center; gap: 4px;
    font-size: 10.5px; font-weight: 700; color: var(--ink); letter-spacing: 0.3px;
  }
  .brand__dot { width: 8px; height: 8px; border-radius: 50%; background: var(--brand-red); }
  .nav { list-style: none; }
  .nav__item {
    position: absolute; left: 14px;
    display: flex; align-items: center; gap: 8px;
    font-size: 6.8px; color: var(--ink); letter-spacing: 0.2px;
  }
  .nav__item svg { width: 12px; height: 12px; stroke: var(--ink); fill: none; stroke-width: 1.3; }
  .nav__item--active { color: var(--brand-red); }
  .nav__item--active svg { stroke: var(--brand-red); }

  .topbar {
    position: absolute; left: 107px; right: 0; top: 0; height: 26px;
    background: var(--surface);
    box-shadow: 0 1px 2px rgba(0,0,0,0.05);
    z-index: 1;
  }
  .user {
    position: absolute; left: 432px; top: 6px;
    display: flex; align-items: center; gap: 6px;
    font-size: 6px; color: var(--ink); letter-spacing: 0.2px;
  }
  .user__avatar { width: 15px; height: 15px; border-radius: 50%; background: linear-gradient(#c9d6df, #8fa3b1); }
  .logout {
    position: absolute; left: 487px; top: 5px; width: 37px; height: 15px;
    background: var(--brand-red); color: #fff;
    font-size: 6px; font-weight: 700; letter-spacing: 0.2px;
    display: flex; align-items: center; justify-content: center;
  }

  .card {
    position: absolute; width: 111px; height: 191px;
    background: var(--surface); text-align: center;
  }
  .card__image {
    position: absolute; left: 6px; right: 6px; top: 11px; height: 103px;
  }
  .card__title { position: absolute; left: 0; right: 0; top: 122px; font-size: 6.6px; line-height: 8.2px; color: var(--ink-soft); }
  .card__price { position: absolute; left: 0; right: 0; top: 146px; font-size: 8.4px; font-weight: 500; color: var(--ink-soft); }
  .card__button {
    position: absolute; left: 34px; top: 164px; width: 46px; height: 14px;
    border: 1px solid var(--brand-red); color: var(--brand-red);
    font-size: 6px; display: flex; align-items: center; justify-content: center;
  }
  .view-all {
    position: absolute; left: 332px; top: 470px; width: 77px; height: 18px;
    background: var(--brand-red); color: #fff; font-size: 6px; font-weight: 700; letter-spacing: 0.2px;
    display: flex; align-items: center; justify-content: center;
  }

  .cart-item {
    position: absolute; left: 131px; width: 491px; height: 107px;
    background: var(--surface);
  }
  .cart-item__image { position: absolute; left: 18px; top: 13px; width: 78px; height: 79px; }
  .cart-item__title { position: absolute; left: 127px; top: 22px; font-size: 9.2px; color: var(--ink-soft); }
  .cart-item__price { position: absolute; left: 127px; top: 42px; font-size: 9.2px; font-weight: 500; color: var(--ink-soft); }
  .cart-item__remove {
    position: absolute; left: 127px; top: 66px; width: 40px; height: 14px;
    border: 1px solid var(--brand-red); color: var(--brand-red); font-size: 6.2px;
    display: flex; align-items: center; justify-content: center;
  }
  .qty { position: absolute; left: 391px; top: 43px; display: flex; align-items: center; gap: 10px; }
  .qty svg { width: 15px; height: 15px; stroke: var(--ink-soft); fill: none; stroke-width: 1.2; }
  .qty__value { width: 8px; text-align: center; color: var(--brand-red); font-size: 9px; }
  .checkout {
    position: absolute; left: 307px; top: 388px; width: 116px; height: 29px;
    background: var(--brand-red); color: #fff; font-size: 9.2px; font-weight: 500;
    display: flex; align-items: center; justify-content: center;
  }
</style>
</head>
<body>

<svg width="0" height="0" style="position:absolute">
  <defs>
    <symbol id="icon-home" viewBox="0 0 24 24"><path d="M3 11 12 3l9 8v10h-6v-6H9v6H3z"/></symbol>
    <symbol id="icon-box" viewBox="0 0 24 24"><path d="M12 3 3 7.5v9L12 21l9-4.5v-9z M3 7.5 12 12l9-4.5 M12 12v9 M7.5 5.2l9 4.5"/></symbol>
    <symbol id="icon-cart" viewBox="0 0 24 24"><path d="M2 4h3l2.5 11h11L21 7H6.3"/><circle cx="9" cy="19" r="1.4"/><circle cx="17" cy="19" r="1.4"/></symbol>
    <symbol id="icon-pin" viewBox="0 0 24 24"><path d="M14 21s6-6 6-11a6 6 0 0 0-12 0c0 5 6 11 6 11z"/><circle cx="14" cy="10" r="2.2"/><path d="M4 6v2 M4 11v2 M4 16v3h3" stroke-dasharray="1.5 1.5"/></symbol>
    <symbol id="icon-mail" viewBox="0 0 24 24"><rect x="3" y="5" width="18" height="14"/><path d="m3 5 9 8 9-8"/></symbol>
    <symbol id="icon-plus" viewBox="0 0 24 24"><circle cx="12" cy="12" r="10"/><path d="M12 7v10M7 12h10"/></symbol>
    <symbol id="icon-minus" viewBox="0 0 24 24"><circle cx="12" cy="12" r="10"/><path d="M7 12h10"/></symbol>
  </defs>
</svg>

<!-- Products screen -->
<section class="screen screen--products">
  <aside class="sidebar">
    <div class="brand"><span class="brand__dot"></span>DIAMONDLINE</div>
    <ul class="nav">
      <li class="nav__item nav__item--active" style="top:93px"><svg><use href="#icon-home"/></svg>HOME</li>
      <li class="nav__item" style="top:122px"><svg><use href="#icon-box"/></svg>PRODUCTS</li>
      <li class="nav__item" style="top:151px"><svg><use href="#icon-cart"/></svg>MY CART</li>
      <li class="nav__item" style="top:180px"><svg><use href="#icon-pin"/></svg>TRACK ORDERS</li>
      <li class="nav__item" style="top:210px"><svg><use href="#icon-mail"/></svg>CONTACT</li>
    </ul>
  </aside>
  <header class="topbar">
    <div class="user"><span class="user__avatar" role="img" aria-label="User avatar"></span>MARCUS</div>
    <div class="logout">LOGOUT</div>
  </header>

  <article class="card" style="left:131px;top:52px">
    <div class="card__image" role="img" aria-label="Black t-shirt" style="background:radial-gradient(ellipse 42% 48% at 50% 50%, #1a1a1a 60%, #f7f7f7 100%)"></div>
    <p class="card__title">Lorem Ipsum is simply<br>dummy text of the.</p>
    <p class="card__price">$25.55</p>
    <div class="card__button">Add to Cart</div>
  </article>
  <article class="card" style="left:254px;top:52px">
    <div class="card__image" role="img" aria-label="Black baseball cap" style="background:radial-gradient(ellipse 42% 32% at 50% 45%, #1c1c1c 60%, #ffffff 100%)"></div>
    <p class="card__title">Lorem Ipsum is simply<br>dummy text of the.</p>
    <p class="card__price">$25.55</p>
    <div class="card__button">Add to Cart</div>
  </article>
  <article class="card" style="left:379px;top:52px">
    <div class="card__image" role="img" aria-label="Blue and white striped t-shirt" style="background:radial-gradient(ellipse 36% 42% at 50% 45%, #8a93d6 55%, #ffffff 100%)"></div>
    <p class="card__title">Lorem Ipsum is simply<br>dummy text of the.</p>
    <p class="card__price">$25.55</p>
    <div class="card__button">Add to Cart</div>
  </article>
  <article class="card" style="left:503px;top:52px">
    <div class="card__image" role="img" aria-label="Grey baseball cap" style="background:radial-gradient(ellipse 44% 34% at 50% 45%, #7a7a7a 60%, #ffffff 100%)"></div>
    <p class="card__title">Lorem Ipsum is simply<br>dummy text of the.</p>
    <p class="card__price">$25.55</p>
    <div class="card__button">Add to Cart</div>
  </article>

  <article class="card" style="left:131px;top:256px">
    <div class="card__image" role="img" aria-label="Grey t-shirt" style="background:radial-gradient(ellipse 40% 46% at 50% 50%, #9a9a9a 60%, #ffffff 100%)"></div>
    <p class="card__title">Lorem Ipsum is simply<br>dummy text of the.</p>
    <p class="card__price">$25.55</p>
    <div class="card__button">Add to Cart</div>
  </article>
  <article class="card" style="left:254px;top:256px">
    <div class="card__image" role="img" aria-label="Black hoodie with yellow graphic print" style="background:radial-gradient(ellipse 46% 48% at 50% 48%, #c9d630 0%, #111111 45%, #ffffff 100%)"></div>
    <p class="card__title">Lorem Ipsum is simply<br>dummy text of the.</p>
    <p class="card__price">$25.55</p>
    <div class="card__button">Add to Cart</div>
  </article>
  <article class="card" style="left:379px;top:256px">
    <div class="card__image" role="img" aria-label="Royal blue baseball cap" style="background:radial-gradient(ellipse 40% 38% at 50% 45%, #2746b8 60%, #ffffff 100%)"></div>
    <p class="card__title">Lorem Ipsum is simply<br>dummy text of the.</p>
    <p class="card__price">$25.55</p>
    <div class="card__button">Add to Cart</div>
  </article>
  <article class="card" style="left:503px;top:256px">
    <div class="card__image" role="img" aria-label="White baseball cap" style="background:radial-gradient(ellipse 44% 36% at 50% 45%, #e2e2e2 60%, #ffffff 100%)"></div>
    <p class="card__title">Lorem Ipsum is simply<br>dummy text of the.</p>
    <p class="card__price">$25.55</p>
    <div class="card__button">Add to Cart</div>
  </article>

  <div class="view-all">VIEW ALL PRODUCTS</div>
</section>

<!-- Cart screen -->
<section class="screen screen--cart">
  <aside class="sidebar">
    <div class="brand"><span class="brand__dot"></span>DIAMONDLINE</div>
    <ul class="nav">
      <li class="nav__item" style="top:93px"><svg><use href="#icon-home"/></svg>HOME</li>
      <li class="nav__item" style="top:122px"><svg><use href="#icon-box"/></svg>PRODUCTS</li>
      <li class="nav__item nav__item--active" style="top:151px"><svg><use href="#icon-cart"/></svg>MY CART</li>
      <li class="nav__item" style="top:180px"><svg><use href="#icon-pin"/></svg>TRACK ORDERS</li>
      <li class="nav__item" style="top:210px"><svg><use href="#icon-mail"/></svg>CONTACT</li>
    </ul>
  </aside>
  <header class="topbar">
    <div class="user"><span class="user__avatar" role="img" aria-label="User avatar"></span>MARCUS</div>
    <div class="logout">LOGOUT</div>
  </header>

  <article class="cart-item" style="top:55px">
    <div class="cart-item__image" role="img" aria-label="Black t-shirt" style="background:radial-gradient(ellipse 42% 46% at 50% 50%, #1a1a1a 60%, #f7f7f7 100%)"></div>
    <p class="cart-item__title">Lorem Ipsum is simply dummy text of the.</p>
    <p class="cart-item__price">$25.55</p>
    <div class="cart-item__remove">Remove</div>
    <div class="qty"><svg><use href="#icon-plus"/></svg><span class="qty__value">1</span><svg><use href="#icon-minus"/></svg></div>
  </article>
  <article class="cart-item" style="top:171px">
    <div class="cart-item__image" role="img" aria-label="Royal blue baseball cap" style="background:radial-gradient(ellipse 44% 40% at 50% 45%, #2746b8 60%, #ffffff 100%)"></div>
    <p class="cart-item__title">Lorem Ipsum is simply dummy text of the.</p>
    <p class="cart-item__price">$15.55</p>
    <div class="cart-item__remove">Remove</div>
    <div class="qty"><svg><use href="#icon-plus"/></svg><span class="qty__value">1</span><svg><use href="#icon-minus"/></svg></div>
  </article>

  <div class="checkout">Go to Checkout</div>
</section>

</body>
</html>
```